School Communication Email Template

Looking for a designer to create a couple simple email templates that are matching our brand colors and feel. Attached is the default email template that is currently being sent out. Company details can be shared upon request.

Template is to be used within the booking tool we use (snapshot below) and gmail. Template code is in HTML (see screenshot below).
Updates

Template code for website should be in HTML. Sorry if that created confusion.

Target Market(s)

Parents of kids enrolled in our classes

Industry/Entity Type

Kids sport classes

Font styles to use
Serif

Colors
0054AA
0677BA
7BADD7
CADEEF
E8F1F8
FFF300
FFF600
FEFA6F
FFFEC7
FFFEE8

Requirements
Must have
• Consistency with company brand/colors
Nice to have
• Flexibility to be adjusted as needed

```html
<!DOCTYPE html>
<html lang="en">
<head>
<meta charset="utf-8">
<title>Booking Confirmation Email</title>
<link rel="stylesheet" href="https://fonts.googleapis.com/css2?family=Arvo:wght@700&family=Poppins:wght@400;500;600&display=swap">
<style>
:root{
  --navy:#233a85;
  --sky:#5fb3d9;
  --sky-pale:#e0f3fc;
  --sky-line:#bfe3f3;
  --gold:#f8bc2a;
  --bronze:#c98a2a;
  --ink:#333333;
  --rule:#dddddd;
  --frame:#c5cbe0;
  --white:#ffffff;
}
*{margin:0;padding:0;box-sizing:border-box}
html,body{width:1200px;height:3620px;overflow:hidden;background:var(--white)}
body{position:relative;font-family:"Poppins",sans-serif;color:var(--ink)}
.abs{position:absolute}
.brand{left:48px;top:40px;width:412px;height:360px;display:flex;flex-direction:column;align-items:center;justify-content:center;gap:34px}
.brand-dot{width:150px;height:150px;border-radius:50%;background:var(--gold)}
.brand-name{font-family:"Arvo",serif;font-weight:700;font-size:42px;color:var(--navy);letter-spacing:1px}
.sender{left:700px;top:118px;font-size:32px;line-height:48px}
.sender h2{font-family:"Arvo",serif;font-size:34px;font-weight:700;margin-bottom:18px;color:#3a3a3a}
.divider{left:60px;top:502px;width:1080px;height:3px;background:var(--rule)}
.title{left:0;top:580px;width:1200px;text-align:center;font-family:"Arvo",serif;font-weight:700;font-size:48px;color:var(--navy)}
.progress{left:160px;top:720px}
.greeting{left:32px;top:1012px;font-size:30px}
.greeting b,.names{color:var(--navy);font-weight:600}
.intro{left:32px;top:1080px;width:1120px;font-size:29px;line-height:48px}
.intro b{color:#222;font-weight:600}
.details{left:98px;top:1322px;width:1000px;height:1250px;border:3px solid var(--frame);padding:25px 21px}
.details-head{height:148px;background:var(--navy);color:var(--white);font-family:"Arvo",serif;font-weight:700;font-size:48px;letter-spacing:2px;display:flex;align-items:center;justify-content:center;margin-bottom:26px}
.details-grid{display:grid;grid-template-columns:460px 460px;column-gap:34px;row-gap:16px}
.cell{height:114px;display:flex;align-items:center;justify-content:center;font-size:28px}
.label{background:var(--sky);color:var(--white);font-weight:600;font-size:31px}
.value{background:var(--sky-pale);border:3px solid var(--sky-line)}
.manage{left:32px;top:2700px;font-size:30px;line-height:56px}
.manage h3{font-size:31px;font-weight:600;color:var(--navy)}
.manage a{display:block;margin-top:18px;color:var(--sky);font-weight:600;text-decoration:underline}
.manage .ref{margin-top:12px}
.manage .ref b{font-weight:600}
.signoff{left:32px;top:3016px;font-size:30px;line-height:52px}
.signoff .names{font-size:32px}
.footer{left:0;top:3194px;width:1200px;height:232px;background:var(--gold);font-size:28px;line-height:48px;color:#2a2a2a}
.footer .col{position:absolute;top:36px}
.footer .col-left{left:34px}
.footer .col-right{left:644px}
.footer b{font-weight:600}
.social{left:456px;top:3492px;display:flex;gap:28px}
.social span{width:72px;height:72px;border-radius:50%;background:var(--navy);display:block}
.social span+span{margin-left:0}
</style>
</head>
<body>
  <div class="abs brand">
    <div class="brand-dot"></div>
    <div class="brand-name">COMPANY NAME</div>
  </div>

  <div class="abs sender">
    <h2>YOUR COMPANY NAME</h2>
    <p>418 Maple Ridge Ave, Fairview</p>
    <p>Colorado 80000</p>
    <p>(555) 013-0142</p>
  </div>

  <div class="abs divider"></div>

  <h1 class="abs title">Your Booking has been confirmed</h1>

  <svg class="abs progress" width="850" height="110" viewBox="160 720 850 110" aria-label="Booking progress complete">
    <line x1="216" y1="772" x2="922" y2="772" stroke="#c98a2a" stroke-width="3"/>
    <circle cx="216" cy="772" r="26" fill="#c98a2a"/>
    <circle cx="956" cy="772" r="35" fill="#fff" stroke="#c98a2a" stroke-width="3"/>
    <circle cx="956" cy="772" r="27" fill="#f8bc2a"/>
  </svg>

  <p class="abs greeting">Hello <b>Leo Carter</b></p>
  <p class="abs intro">Your Booking confirmed with <b>COMPANY NAME</b>&nbsp; start date: <b>21-02-2023</b> and end date <b>28-02-2023</b>. Please find the details below.</p>

  <section class="abs details">
    <div class="details-head">BOOKING DETAILS</div>
    <div class="details-grid">
      <div class="cell label">Student First Name</div>
      <div class="cell label">Student Last Name</div>
      <div class="cell value">Leo</div>
      <div class="cell value">Carter</div>
      <div class="cell label">Appointment Name</div>
      <div class="cell label">Appointment Service</div>
      <div class="cell value">name of appointment</div>
      <div class="cell value">Service Name</div>
      <div class="cell label">Booking Start Date</div>
      <div class="cell label">Booking End Date</div>
      <div class="cell value">21st Feb, 2023</div>
      <div class="cell value">23rd Feb, 2023</div>
      <div class="cell label">Appointment Start Time</div>
      <div class="cell label">Appointment&nbsp; End Time</div>
      <div class="cell value">Morning 11.00 AM</div>
      <div class="cell value">Afternoon : 4:30 PM</div>
    </div>
  </section>

  <div class="abs manage">
    <h3>Need to make changes to this appointment?</h3>
    <p>Manage or edit your appointment online through YOUR PORTAL NAME</p>
    <a href="#">Manage My Appointment</a>
    <p class="ref"><b>Appointmnet ID:</b> ABCD123456</p>
  </div>

  <div class="abs signoff">
    <p>Thanks</p>
    <p class="names">Your Company Name</p>
  </div>

  <footer class="abs footer">
    <div class="col col-left">
      <b>Your Company Name</b><br>
      418 Maple Ridge Ave, Fairview,<br>
      Colorado 80000
    </div>
    <div class="col col-right">
      (555) 013-0142<br>
      hello@brightstarclasses.example<br>
      www.brightstarclasses.example
    </div>
  </footer>

  <div class="abs social" aria-label="Social links">
    <span></span><span></span><span></span>
  </div>
</body>
</html>
```